TWPC Business Card Design

Business card for sole operator professional civil and traffic engineer.
Clients are developers and planners who require assistance with traffic strategic master planning advice and design development for access and infrastructure associated with the development.
Colours already in use are greens for the business name and black for other legend. The attached file shows the letterhead template which is currently in use.
Target Market(s)
Professional Clients in development industry
Most clients known to the Principal and card is mostly required to allow ongoing contact
Industry/Entity Type
Business
Contact Information for Business Card
LACHLAN PETTIGREW CONSULTING PARTNERS
ABN 37 814 529 106
PO Box 418 KELWOOD NSW 2619
Lachlan Pettigrew 0412 358 971
l.pettigrew@corvanmail.net

```html
<!DOCTYPE html>
<html lang="en">
<head>
<meta charset="utf-8">
<title>TWPC Business Card</title>
<link rel="stylesheet" href="https://fonts.googleapis.com/css2?family=Arimo:wght@400&display=swap">
<style>
  :root {
    --page-bg: #d9d9d6;
    --card-lime: #8fcb22;
    --card-lime-light: #a9dc47;
    --ink: #111111;
  }
  * { margin: 0; padding: 0; box-sizing: border-box; }
  html, body {
    width: 1200px;
    height: 960px;
    overflow: hidden;
    background: var(--page-bg);
    font-family: "Arimo", Arial, sans-serif;
    color: var(--ink);
  }
  .business-card {
    position: absolute;
    left: 100px;
    top: 167px;
    width: 1000px;
    height: 625px;
    overflow: hidden;
    background: linear-gradient(160deg, var(--card-lime-light) 0%, var(--card-lime) 55%, var(--card-lime) 100%);
    box-shadow: 0 10px 30px rgba(0,0,0,0.25);
  }
  .firm-name {
    position: absolute;
    left: 82px;
    right: 40px;
    top: 92px;
    font-size: 35px;
    letter-spacing: 0;
    white-space: nowrap;
  }
  .principal-name {
    position: absolute;
    right: 40px;
    top: 224px;
    font-size: 30px;
    white-space: nowrap;
  }
  .divider {
    position: absolute;
    left: 30px;
    right: 0;
    top: 290px;
    height: 5px;
    background: var(--ink);
  }
  .abn {
    position: absolute;
    right: 40px;
    top: 326px;
    font-size: 24px;
  }
  .contact-list {
    position: absolute;
    left: 100px;
    top: 425px;
    list-style: none;
  }
  .contact-item {
    display: flex;
    align-items: center;
    gap: 16px;
    height: 52px;
    font-size: 27px;
  }
  .contact-icon { width: 28px; height: 28px; flex: none; }
</style>
</head>
<body>
  <div class="business-card">
    <p class="firm-name">LACHLAN PETTIGREW CONSULTING PARTNERS</p>
    <p class="principal-name">LACHLAN PETTIGREW</p>
    <div class="divider"></div>
    <p class="abn">ABN 37 814 529 106</p>
    <ul class="contact-list">
      <li class="contact-item">
        <svg class="contact-icon" viewBox="0 0 24 24" aria-hidden="true">
          <path d="M2 9c0-3 4-5 10-5s10 2 10 5v2h-5V8.5c-1.5-.6-3.2-.9-5-.9s-3.5.3-5 .9V11H2z" fill="#111"/>
          <path d="M6 12l2-3h8l2 3v8H6z" fill="#111"/>
          <circle cx="12" cy="15.5" r="2.2" fill="#8fcb22"/>
        </svg>
        <span>0412 358 971</span>
      </li>
      <li class="contact-item">
        <svg class="contact-icon" viewBox="0 0 24 24" aria-hidden="true">
          <rect x="2" y="5" width="20" height="14" fill="#111"/>
          <path d="M2.5 5.5L12 13l9.5-7.5" fill="none" stroke="#8fcb22" stroke-width="1.6"/>
        </svg>
        <span>l.pettigrew@corvanmail.net</span>
      </li>
      <li class="contact-item">
        <svg class="contact-icon" viewBox="0 0 24 24" aria-hidden="true">
          <path d="M12 2a7 7 0 0 0-7 7c0 5 7 13 7 13s7-8 7-13a7 7 0 0 0-7-7z" fill="#111"/>
          <circle cx="12" cy="9" r="2.6" fill="#8fcb22"/>
        </svg>
        <span>418 KELWOOD NSW 2619</span>
      </li>
    </ul>
  </div>
</body>
</html>
```